Business cards in digital learning for freelancer

Hello, I need a business cards in french. I work in the Digital learning industries as freeelancer; I'm an expert in digital learning. I work in France. My customer are in the health industry, pharmaceutical industry, and training organization. I've got a logo. I offer three services: consulting, Design, and Training. In the consulting, I offers coaching to choose your digital learning tools and the digital learning strategy. For the Design, I product differents level of elearning like rapid-learning, elearning, micro-learning, video-learning. And for the training service, I've create training about pedagogy, digital learning management project, Digital learning design.
I join my Logo create in this platform. My universe is gamified. I like the life, and I'm very social. I want a card like I'm I. I love Art (painting), Europeen comics. I use in my visual support "permanent maker" font and caracters. I would like cards: elegant, modern, Top class. If you need any information, you can ask me.
thanks for ideas

Target Market(s)

in health industries and training organization for Training manager, instructor, human resources director

Contact Information for Business Card

Phone number : 06 71 38 95 14 , mail: bastiengolmier@quelmoto.fr, web: bastiengolmier.fr , Carrivo

Font styles to use
Sans Serif

Requirements
Must have
• Use my logo and write my 3 services (consulting, training, design)

```html
<!DOCTYPE html>
<html lang="fr">
<head>
<meta charset="utf-8">
<title>Golmier – cartes de visite</title>
<link rel="stylesheet" href="https://fonts.googleapis.com/css2?family=Arimo:wght@400;700&family=Marcellus+SC&display=swap">
<style>
  :root {
    --orange: #f37325;
    --grey-band: #6f6f6f;
    --text-grey: #4a4a4a;
    --rule-grey: #9a9a9a;
    --white: #ffffff;
    --backdrop: #2e2e2e;
  }
  * { box-sizing: border-box; margin: 0; padding: 0; }
  html, body { width: 1200px; height: 1015px; overflow: hidden; }
  body {
    background: var(--backdrop);
    font-family: "Arimo", Arial, sans-serif;
    position: relative;
  }
  .card {
    position: absolute;
    left: 250px;
    width: 700px;
    height: 400px;
    overflow: hidden;
    box-shadow: 0 10px 30px rgba(0,0,0,.55);
  }
  /* ---------- front ---------- */
  .card--front { top: 80px; background: var(--orange); }
  .brand {
    position: absolute;
    display: flex;
    align-items: center;
    gap: 18px;
  }
  .brand__dot {
    width: 70px; height: 70px; border-radius: 50%;
    border: 14px solid currentColor;
  }
  .brand__name {
    font-family: "Arimo", Arial, sans-serif;
    font-weight: 700;
    font-size: 64px;
    letter-spacing: 2px;
  }
  .card--front .brand {
    color: var(--white);
    left: 50%; top: 130px;
    transform: translateX(-50%);
  }
  .front__band {
    position: absolute; left: 0; right: 0; bottom: 0;
    height: 48px;
    background: var(--grey-band);
    display: flex; align-items: center; justify-content: center; gap: 10px;
    color: var(--white);
    font-size: 15px;
  }
  .front__band-circle {
    width: 26px; height: 26px; border-radius: 50%;
    background: var(--white);
  }
  /* ---------- back ---------- */
  .card--back { top: 535px; background: var(--white); }
  .card--back .brand {
    color: var(--orange);
    left: 40px; top: 140px;
  }
  .card--back .brand__dot { width: 52px; height: 52px; border-width: 10px; }
  .card--back .brand__name { font-size: 46px; }
  .back__divider {
    position: absolute;
    left: 370px; top: 60px;
    width: 1px; height: 200px;
    background: var(--rule-grey);
  }
  .contact {
    position: absolute;
    left: 400px; top: 70px;
    color: var(--text-grey);
  }
  .contact__name {
    font-family: "Marcellus SC", serif;
    color: var(--orange);
    font-size: 28px;
    letter-spacing: 1px;
    line-height: 1;
  }
  .contact__role { font-size: 18px; margin-top: 4px; }
  .contact__list { list-style: none; margin-top: 40px; font-size: 17px; }
  .contact__list li {
    display: flex; align-items: center; gap: 10px;
    height: 27px;
  }
  .contact__list svg { width: 18px; height: 18px; flex: none; }
  .contact__accent { color: var(--orange); }
  .back__band {
    position: absolute; left: 0; right: 0; bottom: 0;
    height: 70px;
    background: var(--orange);
    color: var(--white);
    display: flex; align-items: center; justify-content: flex-end;
    padding-right: 60px;
    font-size: 18px;
    letter-spacing: .5px;
  }
  .back__band .sep {
    display: inline-block; width: 11px; height: 11px;
    border-radius: 50%; background: var(--white);
    margin: 0 6px; vertical-align: middle;
  }
</style>
</head>
<body>

<section class="card card--front" aria-label="Recto">
  <div class="brand">
    <span class="brand__dot"></span>
    <span class="brand__name">GOLMIER</span>
  </div>
  <div class="front__band">
    <span class="front__band-circle"></span>
    <span>Carrivo</span>
  </div>
</section>

<section class="card card--back" aria-label="Verso">
  <div class="brand">
    <span class="brand__dot"></span>
    <span class="brand__name">GOLMIER</span>
  </div>

  <div class="back__divider"></div>

  <div class="contact">
    <p class="contact__name">Julien Marsac</p>
    <p class="contact__role">Managing Director</p>
    <ul class="contact__list">
      <li>
        <svg viewBox="0 0 24 24" aria-hidden="true"><path fill="#f37325" d="M6.6 10.8a15 15 0 0 0 6.6 6.6l2.2-2.2c.3-.3.7-.4 1-.2 1.1.4 2.3.6 3.6.6.6 0 1 .4 1 1V20c0 .6-.4 1-1 1A17 17 0 0 1 3 4c0-.6.4-1 1-1h3.5c.6 0 1 .4 1 1 0 1.3.2 2.5.6 3.6.1.3 0 .7-.2 1z"/></svg>
        <span>06 71 38 95 14</span>
      </li>
      <li>
        <svg viewBox="0 0 24 24" aria-hidden="true"><rect x="2" y="5" width="20" height="14" fill="#f37325"/><path d="M2 5l10 8 10-8" fill="none" stroke="#fff" stroke-width="1.8"/></svg>
        <span>bastiengolmier@quelmoto.fr</span>
      </li>
      <li>
        <svg viewBox="0 0 24 24" aria-hidden="true"><g fill="none" stroke="#f37325" stroke-width="2"><circle cx="12" cy="12" r="9"/><ellipse cx="12" cy="12" rx="4" ry="9"/><path d="M3 12h18M5 7h14M5 17h14"/></g></svg>
        <span>www.<span class="contact__accent">bastiengolmier</span>.fr</span>
      </li>
    </ul>
  </div>

  <div class="back__band">
    CONSULTING <span class="sep"></span> TRAINING <span class="sep"></span> DESIGN
  </div>
</section>

</body>
</html>
```